One of a kind service business!

We are the only ocean freight auditing company in the entire world that does what we do. We provide a innovative service in auditing our clients invoices for billing errors as it relates to the import and export of their products anywhere in the world. We'd like to retain the current logo - but we are open to any interesting concepts that can complete the card.

Target Market(s)

C-Level and Senior Financial executives

Industry/Entity Type

Auditing

Requirements
Must have

• ONE SIDED ONLY
Should not have
• no cartoonish images

```html
<!DOCTYPE html>
<html lang="en">
<head>
<meta charset="utf-8">
<title>Tidewater Review – Business Card</title>
<link rel="stylesheet" href="https://fonts.googleapis.com/css2?family=Arimo:wght@400;700&display=swap">
<style>
  :root {
    --page-bg: #d9d9d9;
    --card-white: #ffffff;
    --ocean-blue: #0b7bb0;
    --brand-blue: #1577b0;
    --ink: #1c1c1c;
    --band-black: #1a1714;
    --icon-blue: #1a6ca6;
  }
  * { margin: 0; padding: 0; box-sizing: border-box; }
  html, body {
    width: 1200px; height: 944px; overflow: hidden;
    background: var(--page-bg);
    font-family: "Arimo", Arial, sans-serif;
  }
  .card {
    position: absolute; left: 100px; top: 186px;
    width: 1000px; height: 572px;
    background: var(--card-white);
    border-radius: 30px;
    overflow: hidden;
  }
  .card-waves { position: absolute; inset: 0; }
  .brand {
    position: absolute; left: 52px; top: 86px;
    display: flex; align-items: center; gap: 14px;
    color: var(--brand-blue);
    font-size: 62px; font-weight: 700; letter-spacing: 1px;
    line-height: 1;
  }
  .brand-square { width: 22px; height: 22px; background: var(--brand-blue); }
  .contact {
    position: absolute; left: 70px;
    color: var(--ink); font-size: 28px; line-height: 1;
  }
  .contact-row { position: absolute; left: 0; display: flex; align-items: center; white-space: nowrap; }
  .contact-row svg { width: 22px; height: 22px; margin-right: 18px; fill: var(--icon-blue); flex: none; }
  .address-lines { line-height: 33px; }
  .address-lines span { display: block; }
  .address-row { align-items: flex-start; }
  .address-row svg { margin-top: 4px; }
  .person {
    position: absolute; left: 680px; width: 280px; top: 460px;
    text-align: center; color: #ffffff;
  }
  .person-name { font-size: 36px; }
  .person-role { font-size: 25px; margin-top: 10px; }
</style>
</head>
<body>
  <article class="card">
    <svg class="card-waves" viewBox="0 0 1000 572" preserveAspectRatio="none" aria-hidden="true">
      <path fill="var(--band-black)" d="M708 0 C640 40 620 140 610 240 C600 360 570 480 494 572 L1000 572 L1000 0 Z"/>
      <path fill="var(--ocean-blue)" d="M742 0 C700 50 690 160 670 260 C650 370 630 470 596 572 L1000 572 L1000 0 Z"/>
    </svg>

    <div class="brand">
      <span class="brand-name">Tidewater Review</span>
      <span class="brand-square"></span>
    </div>

    <div class="contact" style="top:216px;">
      <div class="contact-row address-row" style="top:0;">
        <svg viewBox="0 0 20 20"><path d="M10 2 L19 10 H16 V18 H12 V13 H8 V18 H4 V10 H1 Z"/></svg>
        <div class="address-lines">
          <span>Harbor Point Center</span>
          <span>Lodni 12, Prague</span>
          <span>Czech Republic 11040</span>
        </div>
      </div>
      <div class="contact-row" style="top:112px;">
        <svg viewBox="0 0 20 20"><path d="M5 2 C3 3 2 6 3 9 C5 14 9 17 13 18 C15 18 17 17 18 15 L14 12 L12 14 C9 13 7 11 6 8 L8 6 Z"/></svg>
        <span>+420 222 555 018</span>
      </div>
      <div class="contact-row" style="top:146px;">
        <svg viewBox="0 0 20 20"><path d="M6 1 H14 V19 H6 Z M8 4 V14 H12 V4 Z"/></svg>
        <span>+420 608 555 274</span>
      </div>
      <div class="contact-row" style="top:180px;">
        <svg viewBox="0 0 20 20"><path d="M5 2 C3 3 2 6 3 9 C5 14 9 17 13 18 C15 18 17 17 18 15 L14 12 L12 14 C9 13 7 11 6 8 L8 6 Z"/></svg>
        <span>+1 646 555 0193 - USA</span>
      </div>
      <div class="contact-row" style="top:214px;">
        <svg viewBox="0 0 20 20"><path d="M6 2 H14 V7 H6 Z M2 8 H18 V16 H2 Z M5 13 H15 V18 H5 Z"/></svg>
        <span>+420 221 555 306</span>
      </div>
      <div class="contact-row" style="top:248px;">
        <svg viewBox="0 0 20 20"><circle cx="10" cy="10" r="8.5"/><path d="M2 10 H18 M10 1.5 C6 6 6 14 10 18.5 M10 1.5 C14 6 14 14 10 18.5" stroke="#fff" stroke-width="1.4" fill="none"/></svg>
        <span>www.tidewaterreview.net</span>
      </div>
      <div class="contact-row" style="top:282px;">
        <svg viewBox="0 0 20 20"><path d="M1 4 H19 V16 H1 Z"/><path d="M1.5 4.5 L10 11 L18.5 4.5" stroke="#fff" stroke-width="1.6" fill="none"/></svg>
        <span>marekh@tidewaterreview.net</span>
      </div>
    </div>

    <div class="person">
      <div class="person-name">Marek Holloway</div>
      <div class="person-role">CEO</div>
    </div>
  </article>
</body>
</html>
```